"Inkvale" printing shop

-The design must be based around the attached HPID (home page information design) called "Inkvale - Print Studio".

The table boxes are just for approximate placement of information – you DON'T have to box everything in and you can arrange these. All fonts used in the HPID are only examples - you can use any Google font you wish.

- Information only is in orange text. Copy to go on the design in black text. Some instructions are in the HPID. Please be creative!

-The design needs to be modern. Colours are to be consistent with their new logo or complement it. Keep it clean and simple, you don't need to use lots of colours. Use lots of white.

- images / icons for the site need to be relevant and high quality, but they must also be free images or icons. I have attached a few examples that could be used.

Width of content will be 1100 pixels when implemented as a web page. Header height (without nav bar) 150-200 pixels.

If your design is chosen the winning PSD file will have to be provided as follows…
1. Canvas size of 2000px x 2000px - 72ppi in Adobe Photoshop (CS5 compatible)
2. Width of content section is 1100px wide - centered in the canvas
3. Any button rollovers/hovers in the PSD as hidden layers.
4. All fonts used must be Google fonts.
5. You will need to supply the chosen home page plus one example page (example page as a style guide for how all other pages will look). Example page is only the header and navigational bar at the top, an empty sector in the middle with a column (190 px wide) which can be left or right aligned which means the main sector is 910 pixels wide, and then the footer at the bottom of the page

Checklist - http://pagebuildertally.example/

Examples of some websites that have great design... don't copy them please but they are similar in look to what we are after....
http://www.rookfenly.example/

Industry/Entity Type

Printing

Font styles to use
Serif
Sans Serif

Requirements
Should not have
• Drop shadows, comic sans font

```html
<!DOCTYPE html>
<html lang="en">
<head>
<meta charset="utf-8">
<title>Inkvale - Printing Shop</title>
<link href="https://fonts.googleapis.com/css2?family=Lato:wght@300;400;700;900&family=Raleway:wght@400;500;700&display=swap" rel="stylesheet">
<style>
:root{
  --green:#7ab034;
  --green-dark:#5a8a25;
  --green-ink:#557a2c;
  --green-pale:#cde3b3;
  --grey-bg:#eeeded;
  --hero-bg:#efefef;
  --ink:#333333;
  --text:#3d3d3d;
  --footer:#333333;
  --white:#ffffff;
}
*{margin:0;padding:0;box-sizing:border-box}
html,body{width:1200px;height:2350px;overflow:hidden}
body{position:relative;background:var(--white);font-family:'Lato',sans-serif;color:var(--text)}
.abs{position:absolute}

/* header */
.site-header{position:absolute;left:0;top:0;width:1200px;height:137px;background:var(--white)}
.brand{left:124px;top:38px;display:flex;align-items:center;gap:10px}
.brand-dot{width:56px;height:56px;border-radius:50%;background:var(--green)}
.brand-name{font-family:'Lato',sans-serif;font-weight:900;font-size:34px;color:var(--green)}
.tagline{left:346px;top:28px}
.tagline h1{font-family:'Raleway',sans-serif;font-weight:500;font-size:35px;letter-spacing:3px;color:var(--ink)}
.tagline p{font-family:'Raleway',sans-serif;font-size:16px;color:var(--ink);margin-top:4px}
.contact{left:929px;top:36px;font-size:14px;color:var(--text);line-height:19px}
.contact .row{display:flex;gap:8px;align-items:flex-start}
.contact .row+.row{margin-top:14px}
.contact svg{width:13px;height:14px;margin-top:2px;fill:#555}

/* nav bars */
.nav{position:absolute;left:0;width:1200px;background:var(--green);border-top:1px solid var(--green-dark);border-bottom:1px solid var(--green-dark)}
.nav ul{list-style:none;display:flex;width:952px;margin:0 auto;height:100%}
.nav li{flex:1;display:flex;align-items:center;justify-content:center;color:var(--white);font-size:14px;border-left:1px solid var(--green-dark)}
.nav li:last-child{border-right:1px solid var(--green-dark)}
.nav-main{top:137px;height:46px}
.nav-sub{top:654px;height:44px}
.nav-sub li{font-size:13.5px}

/* hero */
.hero{position:absolute;left:0;top:183px;width:1200px;height:471px;background:var(--hero-bg)}
.hero-copy{left:121px;top:88px;font-family:'Raleway',sans-serif;color:var(--green)}
.hero-copy .line{font-size:35px;line-height:60px}
.hero-copy .line.strong{font-weight:700}
.btn-more{left:126px;top:286px;width:118px;height:33px;background:var(--green);color:var(--white);font-size:13px;display:flex;align-items:center;justify-content:center;gap:6px}
.btn-more svg{width:12px;height:12px}
.hero-visual{left:505px;top:40px;width:566px;height:409px}

/* services */
.services{position:absolute;left:0;top:698px;width:1200px;height:582px;background:var(--grey-bg)}
.tile{position:absolute;width:301px;height:215px;background:var(--green);border-radius:4px 4px 0 0;border-bottom:4px solid var(--green-ink)}
.tile .badge{position:absolute;left:82px;top:20px;width:138px;height:138px;border-radius:50%;background:var(--white);display:flex;align-items:center;justify-content:center}
.tile .badge svg{width:70px;height:70px;fill:var(--green-ink)}
.tile .label{position:absolute;left:0;bottom:0;width:100%;height:45px;background:var(--green-pale);display:flex;align-items:center;justify-content:center;font-size:21px;font-weight:700;color:var(--ink)}

/* features */
.feature{position:absolute;width:271px;height:195px;border:2px solid var(--green);background:var(--white)}
.feature .ring{position:absolute;left:-29px;top:40px;width:57px;height:57px;border-radius:50%;background:var(--white);border:2px solid var(--green);display:flex;align-items:center;justify-content:center}
.feature .ring span{width:45px;height:45px;border-radius:50%;background:var(--green);display:flex;align-items:center;justify-content:center}
.feature .ring svg{width:26px;height:26px;fill:var(--white)}
.feature h3{position:absolute;left:36px;top:22px;font-size:16px;font-weight:700;color:var(--green-ink)}
.feature p{position:absolute;left:36px;top:48px;width:218px;font-size:13px;line-height:19px;text-align:justify;hyphens:auto;-webkit-hyphens:auto;color:var(--text)}
.feature .more{position:absolute;left:36px;top:158px;font-size:13px;font-weight:700;color:var(--green-ink)}

/* footer */
.site-footer{position:absolute;left:0;top:1819px;width:1200px;height:531px;background:var(--footer);color:var(--white)}
.quote{left:124px;top:34px;width:384px}
.quote h2,.enquiry h2{font-size:22px;font-weight:700;color:var(--white)}
.quote p{font-size:17px;font-weight:300;line-height:18px;color:#e8e8e8;margin-top:30px;text-align:justify}
.quote p+p{margin-top:16px}
.social{left:133px;top:221px;display:flex;gap:18px}
.social span{width:35px;height:35px;border:2px solid var(--white);transform:rotate(45deg)}
.enquiry{left:531px;top:34px}
.field{position:absolute;height:33px;border:1px solid #cfcfcf;background:var(--footer);color:var(--white);font-size:12px;padding:10px 8px}
.send{position:absolute;left:767px;top:274px;width:83px;height:31px;background:var(--green);color:var(--white);font-size:13px;font-weight:700;display:flex;align-items:center;justify-content:center}
.foot-nav{position:absolute;left:0;top:410px;width:1200px;height:63px;background:var(--green);display:flex;align-items:center}
.foot-nav ul{list-style:none;display:flex;width:952px;margin:0 auto;font-size:10px;color:var(--white)}
.foot-nav li{white-space:nowrap}
.foot-nav li+li::before{content:"|";margin:0 5px}
.copyright{position:absolute;left:0;top:473px;width:1200px;height:58px;display:flex;align-items:center;justify-content:center;font-size:13px;color:#bdbdbd}
</style>
</head>
<body>

<header class="site-header">
  <div class="abs brand"><span class="brand-dot"></span><span class="brand-name">Inkvale</span></div>
  <div class="abs tagline">
    <h1>Duplication is our vocation</h1>
    <p>Professional photocopying - digital &amp; film processing, design and printing</p>
  </div>
  <div class="abs contact">
    <div class="row"><svg viewBox="0 0 24 24"><path d="M6.6 10.8a15 15 0 0 0 6.6 6.6l2.2-2.2a1 1 0 0 1 1-.25 11.4 11.4 0 0 0 3.6.57 1 1 0 0 1 1 1V20a1 1 0 0 1-1 1A17 17 0 0 1 3 4a1 1 0 0 1 1-1h3.5a1 1 0 0 1 1 1c0 1.25.2 2.450.57 3.57a1 1 0 0 1-.25 1z"/></svg><span>07 555 0148</span></div>
    <div class="row"><svg viewBox="0 0 24 24"><path d="M12 2a7 7 0 0 0-7 7c0 5.25 7 13 7 13s7-7.75 7-13a7 7 0 0 0-7-7zm0 9.5A2.5 2.5 0 1 1 12 6.5a2.5 2.5 0 0 1 0 5z"/></svg><span>7/52 Harbour Road<br>&nbsp;&nbsp;&nbsp;Westbay - Kerrmouth</span></div>
  </div>
</header>

<nav class="nav nav-main">
  <ul><li>Home</li><li>About</li><li>Photocopying</li><li>Printing</li><li>laminating</li><li>Business Cards</li><li>Typing Services</li></ul>
</nav>

<section class="hero">
  <div class="abs hero-copy">
    <div class="line strong">Digital printing Laminating</div>
    <div class="line">Photocopying Services</div>
    <div class="line">Throughout Kerrmouth</div>
  </div>
  <div class="abs btn-more">READ MORE <svg viewBox="0 0 12 12"><circle cx="6" cy="6" r="6" fill="#fff"/><path d="M5 3.5 7.5 6 5 8.5" stroke="#7ab034" stroke-width="1.6" fill="none"/></svg></div>
  <svg class="abs hero-visual" viewBox="0 0 566 409" role="img" aria-label="Stack of glossy photo prints showing a sunflower and water droplets">
    <defs>
      <linearGradient id="printBack" x1="0" y1="0" x2="1" y2="1"><stop offset="0" stop-color="#e0903a"/><stop offset=".5" stop-color="#4d7a96"/><stop offset="1" stop-color="#1f3f73"/></linearGradient>
      <linearGradient id="printFront" x1="0" y1="0" x2="1" y2="1"><stop offset="0" stop-color="#f5c21c"/><stop offset=".6" stop-color="#d9901a"/><stop offset="1" stop-color="#4f7a2e"/></linearGradient>
    </defs>
    <polygon points="110,60 470,10 560,220 200,330" fill="#ffffff"/>
    <polygon points="126,72 462,26 540,214 210,312" fill="url(#printBack)"/>
    <polygon points="0,180 190,130 270,320 80,380" fill="#ffffff"/>
    <polygon points="14,188 182,144 256,312 90,366" fill="url(#printFront)"/>
  </svg>
</section>

<nav class="nav nav-sub">
  <ul><li>Film Processing</li><li>Photo Printing</li><li>Passport Photos</li><li>Image restoration</li><li>Printer Supplies</li><li>Free Quote</li><li>Contact</li></ul>
</nav>

<section class="services">
  <div class="tile" style="left:124px;top:48px">
    <div class="badge"><svg viewBox="0 0 70 70"><path d="M10 22 35 12 60 22 35 32z"/><path d="M10 34 16 31.5 35 39 54 31.5 60 34 35 44z"/><path d="M10 46 16 43.5 35 51 54 43.5 60 46 35 56z"/></svg></div>
    <div class="label">Photocopying</div>
  </div>
  <div class="tile" style="left:450px;top:48px">
    <div class="badge"><svg viewBox="0 0 70 70"><rect x="12" y="20" width="40" height="30" rx="3"/><rect x="52" y="14" width="8" height="42" rx="2"/><rect x="20" y="50" width="20" height="10"/></svg></div>
    <div class="label">Laminating &amp; Binding</div>
  </div>
  <div class="tile" style="left:775px;top:48px">
    <div class="badge"><svg viewBox="0 0 70 70"><rect x="22" y="10" width="26" height="18" fill="none" stroke="#557a2c" stroke-width="3"/><rect x="12" y="30" width="46" height="22" rx="3"/><rect x="20" y="46" width="30" height="12" fill="#fff" stroke="#557a2c" stroke-width="3"/></svg></div>
    <div class="label">Digital Printing</div>
  </div>
  <div class="tile" style="left:124px;top:300px">
    <div class="badge"><svg viewBox="0 0 70 70"><circle cx="35" cy="35" r="26"/><circle cx="35" cy="35" r="6" fill="#fff"/><path d="M35 15v12M20 45l10-6M50 45l-10-6" stroke="#fff" stroke-width="5"/></svg></div>
    <div class="label">Film Processing</div>
  </div>
  <div class="tile" style="left:450px;top:300px">
    <div class="badge"><svg viewBox="0 0 70 70"><rect x="10" y="16" width="50" height="38" rx="5" fill="none" stroke="#557a2c" stroke-width="4"/><rect x="18" y="26" width="10" height="6"/><rect x="32" y="26" width="20" height="6"/><rect x="18" y="38" width="34" height="6"/></svg></div>
    <div class="label">Business Cards</div>
  </div>
  <div class="tile" style="left:775px;top:300px">
    <div class="badge"><svg viewBox="0 0 70 70"><rect x="20" y="10" width="30" height="14" rx="2"/><rect x="12" y="26" width="46" height="20" rx="3"/><path d="M20 46h30v14H26l-6-6z" fill="#fff" stroke="#557a2c" stroke-width="3"/></svg></div>
    <div class="label">Photo Printing</div>
  </div>
</section>

<section class="features">
  <article class="feature" style="left:154px;top:1323px">
    <div class="ring"><span><svg viewBox="0 0 26 26"><rect x="7" y="3" width="12" height="6"/><rect x="3" y="10" width="20" height="9" rx="2"/><rect x="7" y="17" width="12" height="6"/></svg></span></div>
    <h3>Cost effective photocopying</h3>
    <p>No matter the quantity of photocopies you need or the size of your copy - you can rely on us to provide a top quality service!</p>
    <span class="more">Read More &raquo;</span>
  </article>
  <article class="feature" style="left:479px;top:1323px">
    <div class="ring"><span><svg viewBox="0 0 26 26"><rect x="7" y="3" width="12" height="6"/><rect x="3" y="10" width="20" height="9" rx="2"/><rect x="7" y="17" width="12" height="6"/></svg></span></div>
    <h3>All digital format printing</h3>
    <p>Either email us your file or bring it into the store and we can get you the print you need. All prints are to the highest qualit</p>
    <span class="more">Read More &raquo;</span>
  </article>
  <article class="feature" style="left:805px;top:1323px">
    <div class="ring"><span><svg viewBox="0 0 26 26"><rect x="4" y="7" width="15" height="12" rx="2"/><rect x="19" y="5" width="3" height="16"/><rect x="7" y="19" width="7" height="4"/></svg></span></div>
    <h3>Laminating and binding</h3>
    <p>Create a professional image for your documents or books. Lamination and binding also keeps your documents well protected</p>
    <span class="more">Read More &raquo;</span>
  </article>
  <article class="feature" style="left:154px;top:1537px">
    <div class="ring"><span><svg viewBox="0 0 26 26"><rect x="3" y="6" width="20" height="14" rx="2" fill="none" stroke="#fff" stroke-width="2"/><rect x="6" y="10" width="5" height="3"/><rect x="13" y="10" width="7" height="3"/><rect x="6" y="15" width="14" height="2"/></svg></span></div>
    <h3>Personal desktop publishing</h3>
    <p>From personalised brochures, posters and birthday and special occasion cards to top quality, cheap business cards - you get it all</p>
    <span class="more">Read More &raquo;</span>
  </article>
  <article class="feature" style="left:479px;top:1537px">
    <div class="ring"><span><svg viewBox="0 0 26 26"><circle cx="13" cy="13" r="10" fill="none" stroke="#fff" stroke-width="2.5"/><circle cx="13" cy="8" r="2.2"/><circle cx="8.5" cy="15.5" r="2.2"/><circle cx="17.5" cy="15.5" r="2.2"/></svg></span></div>
    <h3>Film photo processing</h3>
    <p>Bring in your film to the store and we will work with you to get the best quality print for your purpose and needs. We work with it al</p>
    <span class="more">Read More &raquo;</span>
  </article>
  <article class="feature" style="left:805px;top:1537px">
    <div class="ring"><span><svg viewBox="0 0 26 26"><path d="M3 9 13 5 23 9 13 13z"/><path d="M3 14 6 13 13 16 20 13 23 14 13 18z"/><path d="M3 19 6 18 13 21 20 18 23 19 13 23z"/></svg></span></div>
    <h3>Quality digital photo print</h3>
    <p>Get your photo printed to your requirements - either from a file or from your digital camera. With a wide range of options you can get the print you want</p>
    <span class="more">Read More &raquo;</span>
  </article>
</section>

<footer class="site-footer">
  <div class="abs quote">
    <h2>Get a free quote</h2>
    <p>...or talk to our team about your requirements. Please fill out the form below and we will contact you within a day.</p>
    <p>You can now upload and send us your file for a free quote!</p>
  </div>
  <div class="abs social" aria-label="Social links"><span></span><span></span><span></span><span></span><span></span><span></span></div>
  <div class="abs enquiry"><h2>Equire Form</h2></div>
  <div class="field" style="left:531px;top:90px;width:266px">First Name</div>
  <div class="field" style="left:810px;top:90px;width:266px">Last Name</div>
  <div class="field" style="left:531px;top:132px;width:266px">Number</div>
  <div class="field" style="left:810px;top:132px;width:266px">Email</div>
  <div class="field" style="left:531px;top:175px;width:545px;height:88px">Message</div>
  <div class="send">SEND</div>
  <nav class="foot-nav">
    <ul><li>Home</li><li>About</li><li>Photocopying</li><li>Printing</li><li>Laminating</li><li>Business cards</li><li>Typing services</li><li>Film processing</li><li>Photo Printing</li><li>Passport photos</li><li>Image Restoration</li><li>Printer Supplies</li><li>Free quote</li><li>Contact</li></ul>
  </nav>
  <div class="copyright">Inkvale - Print Studio &copy; copyright 2015 &bull; Privacy Policy</div>
</footer>

</body>
</html>
```